Copper lark buildworks

Copper lark buildworks is a small construction company.
Who is a licenced builder, Carpenter, joiner,
working on heritage ,new build, speacial projects and sometimes furniture

Industry/Entity Type

Construction

```html
<!DOCTYPE html>
<html lang="en">
<head>
<meta charset="utf-8">
<title>Copper lark buildworks – business card</title>
<link href="https://fonts.googleapis.com/css2?family=Exo+2:wght@400;500&family=Lato:wght@400&display=swap" rel="stylesheet">
<style>
  :root {
    --page: #ecebe8;
    --ink: #111111;
    --paper: #ffffff;
    --lime: #7cc242;
    --muted: #222222;
  }
  * { box-sizing: border-box; margin: 0; padding: 0; }
  html, body { width: 1200px; height: 880px; overflow: hidden; background: var(--page); }
  .canvas {
    position: relative; width: 1200px; height: 880px;
    display: flex; flex-direction: column; align-items: center; justify-content: center; gap: 26px;
  }
  .card {
    width: 700px; height: 400px; border-radius: 22px; position: relative;
    box-shadow: 0 6px 18px rgba(0,0,0,.18);
  }
  .card--back { background: var(--ink); display: flex; flex-direction: column; align-items: center; justify-content: center; }
  .card--front { background: var(--paper); }

  .brand { display: flex; align-items: center; gap: 12px; white-space: nowrap; }
  .brand__dot { width: 34px; height: 34px; border-radius: 50%; background: var(--lime); flex: none; }
  .brand__name {
    font-family: "Exo 2", sans-serif; font-weight: 500; font-size: 34px; letter-spacing: .5px;
    color: var(--paper);
  }

  .back__web {
    margin-top: 46px; font-family: "Lato", sans-serif; font-size: 15px; letter-spacing: 4px; color: var(--paper);
  }
  .back__web span { color: var(--lime); }

  .front__brand {
    position: absolute; left: 0; top: 200px; width: 420px;
    justify-content: center;
  }
  .front__brand .brand__dot { width: 26px; height: 26px; }
  .front__brand .brand__name { color: var(--ink); font-size: 24px; }
  .front__rule { position: absolute; left: 420px; top: 92px; width: 1.5px; height: 170px; background: var(--lime); }

  .contact { position: absolute; left: 450px; top: 96px; }
  .contact__name { font-family: "Exo 2", sans-serif; font-size: 24px; color: var(--ink); line-height: 1; }
  .contact__name span { color: var(--lime); }
  .contact__role { font-family: "Exo 2", sans-serif; font-size: 16px; color: var(--muted); margin-top: 2px; }
  .contact__list { list-style: none; margin-top: 16px; }
  .contact__item {
    display: flex; align-items: center; gap: 8px; margin-bottom: 6px; white-space: nowrap;
    font-family: "Lato", sans-serif; font-size: 15px; color: var(--muted);
  }
  .contact__icon { width: 20px; height: 20px; flex: none; }
</style>
</head>
<body>
<main class="canvas">
  <section class="card card--back" aria-label="Card back">
    <div class="brand">
      <span class="brand__dot"></span>
      <span class="brand__name">Copper lark buildworks</span>
    </div>
    <p class="back__web">www.<span>copperlarkbuild</span>.com</p>
  </section>

  <section class="card card--front" aria-label="Card front">
    <div class="brand front__brand">
      <span class="brand__dot"></span>
      <span class="brand__name">Copper lark buildworks</span>
    </div>
    <div class="front__rule"></div>
    <div class="contact">
      <p class="contact__name">Mara <span>Holt</span></p>
      <p class="contact__role">President</p>
      <ul class="contact__list">
        <li class="contact__item">
          <svg class="contact__icon" viewBox="0 0 20 20"><circle cx="10" cy="10" r="9" fill="none" stroke="#7cc242" stroke-width="1.5"/><rect x="7" y="5" width="6" height="10" rx="1" fill="none" stroke="#7cc242" stroke-width="1.4"/></svg>
          0491027364
        </li>
        <li class="contact__item">
          <svg class="contact__icon" viewBox="0 0 20 20"><circle cx="10" cy="10" r="9" fill="none" stroke="#7cc242" stroke-width="1.5"/><rect x="5.5" y="6.5" width="9" height="7" fill="none" stroke="#7cc242" stroke-width="1.3"/><path d="M5.5 6.5 10 10.5 14.5 6.5" fill="none" stroke="#7cc242" stroke-width="1.3"/></svg>
          info@copperlarkbuild.com
        </li>
        <li class="contact__item">
          <svg class="contact__icon" viewBox="0 0 20 20"><circle cx="10" cy="10" r="9" fill="none" stroke="#7cc242" stroke-width="1.5"/><circle cx="10" cy="10" r="5" fill="none" stroke="#7cc242" stroke-width="1.2"/><path d="M5 10h10M10 5c-2 3-2 7 0 10M10 5c2 3 2 7 0 10" fill="none" stroke="#7cc242" stroke-width="1"/></svg>
          www.copperlarkbuild.com
        </li>
      </ul>
    </div>
  </section>
</main>
</body>
</html>
```